Business Card Design

We need a business card designed for our new company. Prefer a black card with white logo & writing.

Contact Information for Business Card

Ted Galloway, address: 7-4812 Fernhollow Road, Abbotsford, BC, V3K 8R2, Office Phone: 604-712-3390, Cell: 604-947-2164, Email: ted@resinworkshub.ca

Colors

Designer to choose only greyscale colors for use in the design.

```html
<!DOCTYPE html>
<html lang="en">
<head>
<meta charset="utf-8">
<title>Resinworks Hub – Business Card</title>
<link rel="stylesheet" href="https://fonts.googleapis.com/css2?family=Poppins:wght@300;400;700&display=swap">
<style>
  :root {
    --backdrop: #232325;
    --card: #1f1f21;
    --card-edge: #3a3a3d;
    --ink: #ffffff;
    --ink-soft: #d9d9d9;
    --ink-muted: #4a4a4e;
    --accent-bar: #f2f2ee;
  }
  * { box-sizing: border-box; margin: 0; padding: 0; }
  html, body {
    width: 1200px; height: 711px; overflow: hidden;
    background: var(--backdrop);
    font-family: "Poppins", sans-serif;
    color: var(--ink);
  }
  .sheet {
    position: relative; width: 1200px; height: 711px;
    display: flex; align-items: center; justify-content: center; gap: 40px;
  }
  .card {
    position: relative; width: 540px; height: 309px;
    background: var(--card);
    border: 1px solid var(--card-edge);
    box-shadow: 0 14px 30px rgba(0,0,0,.55);
    overflow: hidden;
  }

  /* Front */
  .card--front { display: flex; align-items: center; justify-content: center; }
  .wordmark {
    display: flex; align-items: center; gap: 12px;
    font-weight: 700; letter-spacing: .5px; white-space: nowrap;
  }
  .wordmark__square { width: 14px; height: 14px; background: currentColor; }
  .card--front .wordmark { font-size: 38px; color: var(--ink-muted); }

  /* Back */
  .card--back .wordmark {
    position: absolute; left: 34px; top: 112px;
    font-size: 28px; color: var(--ink);
  }
  .accent-bar {
    position: absolute; right: 0; top: 30px;
    width: 14px; height: 56px; background: var(--accent-bar);
  }
  .identity {
    position: absolute; right: 34px; top: 30px; text-align: right;
  }
  .identity__name { font-size: 30px; line-height: 1.05; font-weight: 300; white-space: nowrap; }
  .identity__name strong { font-weight: 700; }
  .identity__role { font-size: 13px; font-weight: 300; color: var(--ink-soft); }

  .address {
    position: absolute; right: 34px; top: 196px; text-align: right;
    font-size: 13px; font-weight: 300; line-height: 1.5; color: var(--ink-soft);
  }
  .contacts {
    position: absolute; left: 34px; bottom: 22px;
    list-style: none; font-size: 14px; font-weight: 300; line-height: 1.5;
  }
  .contacts li { display: flex; align-items: center; gap: 10px; }
  .contacts svg { width: 12px; height: 12px; fill: none; stroke: var(--ink); stroke-width: 1.6; }
</style>
</head>
<body>
<main class="sheet">
  <section class="card card--front" aria-label="Card front">
    <div class="wordmark"><span class="wordmark__square"></span>Resinworks Hub</div>
  </section>

  <section class="card card--back" aria-label="Card back">
    <div class="wordmark"><span class="wordmark__square"></span>Resinworks Hub</div>

    <span class="accent-bar"></span>
    <div class="identity">
      <p class="identity__name"><strong>Ted</strong> Galloway</p>
      <p class="identity__role">Founder &amp; CEO</p>
    </div>

    <p class="address">7-4812 Fernhollow Road,<br>Abbotsford, BC, V3K 8R2.</p>

    <ul class="contacts">
      <li>
        <svg viewBox="0 0 12 12"><path d="M2 1.5h2l1 2.5-1.3 1a6 6 0 0 0 3.3 3.3l1-1.3 2.5 1v2A1 1 0 0 1 9.5 11 8.5 8.5 0 0 1 1 2.5a1 1 0 0 1 1-1z"/></svg>
        604-712-3390
      </li>
      <li>
        <svg viewBox="0 0 12 12"><rect x="3" y="1" width="6" height="10" rx="1"/><path d="M5.5 9h1"/></svg>
        604-947-2164
      </li>
      <li>
        <svg viewBox="0 0 12 12"><circle cx="6" cy="6" r="5"/><path d="M1 6h10M6 1c2 2.5 2 7.5 0 10M6 1c-2 2.5-2 7.5 0 10"/></svg>
        www.resinworkshub.ca
      </li>
      <li>
        <svg viewBox="0 0 12 12"><rect x="1" y="2.5" width="10" height="7"/><path d="M1 2.5l5 4 5-4"/></svg>
        ted@resinworkshub.ca
      </li>
    </ul>
  </section>
</main>
</body>
</html>
```